Business Card Design

New business card design

Target Market(s)

Residential & Commercial Property Managers

Industry/Entity Type

Plumbing Services

Contact Information for Business Card

Name - Rowan Keddle, title - Director, Phone Number - 0431 286 517, email - rowan@tbk-plumbing.com.au, Company ABN - 73 215 904 386,

Font styles to use
Sans Serif

Colors
0054AA
0677BA
7BADD7
CADEEF
E8F1F8

```html
<!DOCTYPE html>
<html lang="en">
<head>
<meta charset="utf-8">
<title>TBK Plumbing Services – Business Card</title>
<link rel="stylesheet" href="https://fonts.googleapis.com/css2?family=Arimo:wght@400;700&display=swap">
<style>
  :root {
    --stage: #3d3d3d;
    --card-white: #ffffff;
    --ink: #1d232b;
    --ink-soft: #4a4f57;
    --brand-blue: #0ea5e4;
    --drop-light: #3c4a58;
    --drop-dark: #11161c;
  }
  * { margin: 0; padding: 0; box-sizing: border-box; }
  html, body {
    width: 1200px; height: 803px; overflow: hidden;
    background: var(--stage);
    font-family: "Arimo", Arial, sans-serif;
  }
  .stage {
    position: relative; width: 1200px; height: 803px;
    display: flex; align-items: center; justify-content: center; gap: 40px;
  }
  .card {
    position: relative; width: 540px; height: 300px;
    border-radius: 22px; overflow: hidden;
  }
  /* Front */
  .card--front { background: var(--card-white); }
  .card__swoosh { position: absolute; inset: 0; width: 100%; height: 100%; }
  .card__person {
    position: absolute; top: 62px; right: 150px; text-align: right;
  }
  .card__name { font-weight: 700; font-size: 22px; color: var(--ink); letter-spacing: 0.2px; }
  .card__title { font-size: 13px; color: var(--brand-blue); margin-top: 2px; }
  .card__brand {
    position: absolute; left: 40px; top: 130px;
    display: flex; align-items: center; gap: 10px;
  }
  .brand-dot { width: 14px; height: 14px; border-radius: 50%; background: var(--brand-blue); }
  .brand-name { font-size: 24px; font-weight: 400; color: var(--ink); letter-spacing: 1px; }
  .card__contact {
    position: absolute; left: 40px; bottom: 34px;
    list-style: none; font-size: 13px; color: var(--ink-soft); line-height: 1.6;
  }
  .card__contact li { display: flex; align-items: center; gap: 8px; }
  .card__contact svg { width: 12px; height: 12px; fill: var(--ink); }
  .card__contact .abn { margin-top: 6px; }
  /* Back */
  .card--back { background: var(--ink); }
  .card__pattern {
    position: absolute; inset: 0;
    background: linear-gradient(135deg, var(--drop-dark) 0%, #1d232b 45%, var(--drop-light) 100%);
  }
  .card__brand--back {
    position: absolute; inset: 0;
    display: flex; align-items: center; justify-content: center; gap: 14px;
  }
  .card__brand--back .brand-name { color: var(--card-white); font-size: 34px; }
  .card__brand--back .brand-dot { width: 18px; height: 18px; }
</style>
</head>
<body>
<main class="stage">
  <section class="card card--front">
    <svg class="card__swoosh" viewBox="0 0 540 300" aria-hidden="true">
      <path d="M250 0 H540 V130 C480 60 380 12 250 0 Z" fill="var(--brand-blue)"/>
      <path d="M330 14 C430 35 510 90 540 140 V300 H440 C500 200 470 80 330 14 Z" fill="var(--card-white)"/>
      <path d="M350 22 C440 45 515 100 540 150 V300 H450 C505 200 480 90 350 22 Z" fill="var(--ink)"/>
    </svg>
    <div class="card__person">
      <p class="card__name">Rowan Keddle</p>
      <p class="card__title">Director</p>
    </div>
    <div class="card__brand">
      <span class="brand-dot"></span>
      <span class="brand-name">TBK Plumbing Services</span>
    </div>
    <ul class="card__contact">
      <li><svg viewBox="0 0 24 24"><path d="M6.6 10.8a15 15 0 0 0 6.6 6.6l2.2-2.2a1 1 0 0 1 1-.25 11.4 11.4 0 0 0 3.6.57 1 1 0 0 1 1 1V20a1 1 0 0 1-1 1A17 17 0 0 1 3 4a1 1 0 0 1 1-1h3.5a1 1 0 0 1 1 1c0 1.25.2 2.45.57 3.6a1 1 0 0 1-.25 1z"/></svg>0431 286 517</li>
      <li><svg viewBox="0 0 24 24"><path d="M2 5h20v14H2z M2 5l10 8 10-8" fill="none" stroke="currentColor"/><path d="M2 5h20v2l-10 7L2 7z"/><path d="M2 8l10 7 10-7v11H2z"/></svg>rowan@tbk-plumbing.com.au</li>
      <li class="abn">ABN - 73 215 904 386</li>
    </ul>
  </section>

  <section class="card card--back">
    <div class="card__pattern" role="img" aria-label="Pattern of embossed water drops across a dark card"></div>
    <div class="card__brand card__brand--back">
      <span class="brand-dot"></span>
      <span class="brand-name">TBK Plumbing Services</span>
    </div>
  </section>
</main>
</body>
</html>
```